Fitness Equipment Repair Business Needs a Catchy New Business Card

We have an existing business card, however, it is quite plain and boring. We are expanding primarily in the commercial area (gyms, studios, apartment complexes etc). The business card will serve as eye candy to those managers/owners that can't be met for a face to face.
Originally I was planning for a brochure as well, but all of our information is better summarized on our website. (brightloopservice.ca).
I would like the card to match the colour scheme of the website and utilize the logo. It should have a professional clean feel to it, however, a little colouring outside the lines wouldn't hurt.
The example card is for my service technician (Colin Marsh). If possible I would like to be able to edit the text to use for more than one person.

Industry/Entity Type

Appliance Repair

Contact Information for Business Card

Clean, crisp and professional but needs to be eye catching. Preferably using the black, white and red colour scheme matching the website. Double sided would be nice, but is not necessary.

Colors
ec1f27
ffffff
000000

Requirements
Must have
• Must be able to edit name, phone number and title to use for multiple people. Must show the company website (brightloopservice.ca).

```html
<!DOCTYPE html>
<html lang="en">
<head>
<meta charset="utf-8">
<title>Bright Loop Service – Business Card</title>
<link rel="stylesheet" href="https://fonts.googleapis.com/css2?family=Marcellus+SC&family=Open+Sans:wght@400;600;700&family=Tinos:wght@700&display=swap">
<style>
  :root {
    --brand-red: #ec1f27;
    --brand-black: #000000;
    --brand-white: #ffffff;
    --card-ink: #1a1a1a;
    --page-bg: #e9e7e4;
    --front-bg: #0d0d0d;
  }
  * { box-sizing: border-box; margin: 0; padding: 0; }
  html, body {
    width: 1200px; height: 900px; overflow: hidden;
    background: var(--page-bg);
  }
  .canvas {
    position: relative; width: 1200px; height: 900px;
  }
  .card {
    position: absolute; left: 250px; width: 700px; height: 400px;
    box-shadow: 0 6px 18px rgba(0,0,0,.18);
    overflow: hidden;
  }
  /* Front side */
  .card--front {
    top: 40px;
    background: radial-gradient(ellipse at 50% 40%, #1b1b1b 0%, var(--front-bg) 70%);
    color: var(--brand-white);
  }
  .front-mark {
    position: absolute; left: 110px; top: 95px;
    display: flex; flex-direction: column; align-items: center; gap: 14px;
  }
  .front-mark__circle {
    width: 120px; height: 120px; border-radius: 50%;
    border: 3px solid var(--brand-white);
  }
  .front-mark__name {
    font-family: "Marcellus SC", serif; font-size: 24px;
    color: var(--brand-red); letter-spacing: 1px;
  }
  .front-wordmark {
    position: absolute; left: 330px; top: 92px;
    font-family: "Marcellus SC", serif; font-size: 48px; line-height: 1.08;
    color: var(--brand-white); letter-spacing: 2px;
  }
  /* Back side */
  .card--back {
    top: 460px;
    background: var(--brand-white);
    color: var(--card-ink);
    font-family: "Open Sans", sans-serif;
  }
  .person {
    position: absolute; left: 56px; top: 52px;
  }
  .person__name { font-size: 22px; font-weight: 700; }
  .person__title { font-size: 15px; margin-top: 2px; margin-left: 6px; }
  .address {
    position: absolute; left: 84px; top: 140px;
    font-size: 18px; line-height: 1.3;
  }
  .contacts {
    position: absolute; left: 84px; top: 222px;
    list-style: none; font-size: 17px; line-height: 1.4;
  }
  .contacts li { display: flex; align-items: center; gap: 10px; }
  .contacts svg { width: 14px; height: 14px; flex: none; }
  .back-mark {
    position: absolute; right: 60px; top: 40px;
    display: flex; flex-direction: column; align-items: center; gap: 12px;
  }
  .back-mark__circle {
    width: 130px; height: 130px; border-radius: 50%;
    background: var(--brand-black);
  }
  .back-mark__name {
    font-family: "Open Sans", sans-serif; font-weight: 700; font-size: 24px;
    color: var(--brand-red);
  }
  .tagline {
    position: absolute; left: 56px; right: 40px; top: 328px;
    font-family: "Tinos", serif; font-weight: 700; font-size: 18px;
    line-height: 1.2; text-transform: uppercase; color: var(--brand-black);
  }
</style>
</head>
<body>
<main class="canvas">
  <section class="card card--front" aria-label="Card front">
    <div class="front-mark">
      <div class="front-mark__circle"></div>
      <span class="front-mark__name">Bright Loop</span>
    </div>
    <h1 class="front-wordmark">Bright<br>Loop<br>Service</h1>
  </section>

  <section class="card card--back" aria-label="Card back">
    <div class="person">
      <p class="person__name">Colin Marsh</p>
      <p class="person__title">Managing Director</p>
    </div>
    <p class="address">1234, Address GoesHere,<br>Country, 12345</p>
    <ul class="contacts">
      <li>
        <svg viewBox="0 0 16 16" aria-hidden="true"><path fill="#000" d="M2 5c0-2 2-3 6-3s6 1 6 3v1h-3V5H5v1H2zM4 7h8l2 7H2z"/></svg>
        (044) 123456789
      </li>
      <li>
        <svg viewBox="0 0 16 16" aria-hidden="true"><rect x="4" y="1" width="8" height="14" rx="1.5" fill="none" stroke="#000" stroke-width="1.6"/><circle cx="8" cy="12.5" r="1" fill="#000"/></svg>
        (044)123456789
      </li>
      <li>
        <svg viewBox="0 0 16 16" aria-hidden="true"><rect x="1" y="3" width="14" height="10" fill="#000"/><path d="M1 3l7 6 7-6" fill="none" stroke="#fff" stroke-width="1.2"/></svg>
        info@youremail.com
      </li>
      <li>
        <svg viewBox="0 0 16 16" aria-hidden="true"><circle cx="8" cy="8" r="7" fill="#000"/><path d="M1 8h14M8 1c-3 3-3 11 0 14M8 1c3 3 3 11 0 14" fill="none" stroke="#fff" stroke-width="1"/></svg>
        www.brightloopservice.ca
      </li>
    </ul>
    <div class="back-mark">
      <div class="back-mark__circle"></div>
      <span class="back-mark__name">Bright Loop</span>
    </div>
    <p class="tagline">When your equipment can't finish their workout,<br>give us a call!</p>
  </section>
</main>
</body>
</html>
```